Lunelle Rosa Hair Fancy Business Card’s

I want my business cards to be elite, original and very classy. I want the business cards to match the colors of my logo and to match the design posted. I would love the design of the picture I posted

I want the card all white .
The dripping on the top of the card I want it to match the pink color in my logo that’s also posted .
I need my logo on the business card !
I need my Instagram- @lunelle.rosa.hair__
And my phone number - 555 207 3962

Target Market(s)

My target market is young woman age 23 to older woman to the age of 65
I want both older and younger women to love my design . I don’t want any cheap looking business cards

Industry/Entity Type

Hair And Beauty

Contact Information for Business Card

Add my logo
Add my Instagram- @lunelle.rosa.hair__
My number - 555 207 3962
My website- www.lunellerosahair.example

Font styles to use
Serif
Script

Colors
ffffff
e667a6
e34298

Requirements
Must have
• The business cards must have my logo, my number , my website, and my Instagram!
Nice to have
• Nice to have glitter words that match my logo
• The business cards must look classy and mature
• I want them to be very unique!!
Should not have
• Should not have any colors that doesn’t match my logo ! This is very important! Please

```html
<!DOCTYPE html>
<html lang="en">
<head>
<meta charset="utf-8">
<title>Lunelle Rosa Hair — Business Card</title>
<link href="https://fonts.googleapis.com/css2?family=Lato:wght@400;700&display=swap" rel="stylesheet">
<style>
  :root {
    --backdrop: #2a2a2a;
    --card-white: #ffffff;
    --brand-pink: #e34298;
    --brand-pink-soft: #e667a6;
    --ink: #555555;
    --rule: #c9c9c9;
    --glitter-dark: #6e6e6e;
    --glitter-mid: #8c8c8c;
    --glitter-light: #a9a9a9;
  }
  * { margin: 0; padding: 0; box-sizing: border-box; }
  html, body {
    width: 1200px; height: 1200px; overflow: hidden;
    background: var(--backdrop);
    font-family: "Lato", Arial, sans-serif;
  }
  .stage { position: relative; width: 1200px; height: 1200px; }

  .card {
    position: absolute; top: 310px;
    width: 366px; height: 594px;
    box-shadow: 0 4px 10px rgba(0,0,0,0.45);
  }
  .card--front { left: 233px; background: var(--card-white); }
  .card--back {
    left: 628px;
    background:
      radial-gradient(circle at 30% 25%, var(--glitter-light), transparent 55%),
      radial-gradient(circle at 70% 75%, var(--glitter-light), transparent 55%),
      linear-gradient(160deg, var(--glitter-mid), var(--glitter-dark) 50%, var(--glitter-mid));
  }

  .wordmark {
    position: absolute; left: 0; width: 100%;
    text-align: center;
    font-weight: 700;
    line-height: 1.05;
    letter-spacing: 1px;
  }
  .wordmark__line { display: block; }
  .wordmark__line--lead { font-size: 44px; }
  .wordmark__line--sub { font-size: 24px; letter-spacing: 10px; margin-top: 8px; }

  .card--front .wordmark { top: 440px; top: 130px; color: var(--brand-pink); }
  .card--back .wordmark { top: 228px; color: var(--card-white); }

  .contact {
    position: absolute; left: 0; top: 382px; width: 100%;
    text-align: center; color: var(--ink);
  }
  .contact__item { position: relative; height: 60px; }
  .contact__divider {
    position: relative; height: 24px;
    display: flex; align-items: center; justify-content: center; gap: 6px;
  }
  .contact__rule { width: 56px; height: 1px; background: var(--rule); }
  .contact__icon { width: 22px; height: 22px; }
  .contact__text { display: block; font-size: 21px; margin-top: 4px; letter-spacing: 0.3px; }
  .contact__text--web { font-size: 19px; }
</style>
</head>
<body>
<main class="stage">

  <section class="card card--front" aria-label="Business card front">
    <h1 class="wordmark">
      <span class="wordmark__line wordmark__line--lead">Lunelle Rosa</span>
      <span class="wordmark__line wordmark__line--sub">HAIR</span>
    </h1>

    <div class="contact">
      <div class="contact__item">
        <div class="contact__divider">
          <span class="contact__rule"></span>
          <svg class="contact__icon" viewBox="0 0 22 22" aria-hidden="true">
            <circle cx="11" cy="11" r="9.5" fill="none" stroke="var(--brand-pink)" stroke-width="1.5"/>
            <path d="M8 6.5 L9.6 6.5 L10.3 8.8 L9.2 9.7 Q10.2 11.9 12.3 12.8 L13.2 11.7 L15.5 12.4 L15.5 14 Q15 15.5 13.5 15.3 Q7.2 14.3 6.7 8 Q6.7 6.6 8 6.5 Z" fill="var(--brand-pink)"/>
          </svg>
          <span class="contact__rule"></span>
        </div>
        <span class="contact__text">555 207 3962</span>
      </div>

      <div class="contact__item">
        <div class="contact__divider">
          <span class="contact__rule"></span>
          <svg class="contact__icon" viewBox="0 0 22 22" aria-hidden="true">
            <g fill="none" stroke="var(--brand-pink)" stroke-width="1.4">
              <circle cx="11" cy="11" r="9.5"/>
              <ellipse cx="11" cy="11" rx="4" ry="9.5"/>
              <line x1="1.5" y1="11" x2="20.5" y2="11"/>
              <line x1="11" y1="1.5" x2="11" y2="20.5"/>
              <path d="M3.5 6.5 H18.5 M3.5 15.5 H18.5"/>
            </g>
          </svg>
          <span class="contact__rule"></span>
        </div>
        <span class="contact__text contact__text--web">www.lunellerosahair.example</span>
      </div>

      <div class="contact__item">
        <div class="contact__divider">
          <span class="contact__rule"></span>
          <svg class="contact__icon" viewBox="0 0 22 22" aria-hidden="true">
            <circle cx="11" cy="11" r="9.5" fill="none" stroke="var(--brand-pink)" stroke-width="1.5"/>
          </svg>
          <span class="contact__rule"></span>
        </div>
        <span class="contact__text">@lunelle.rosa.hair__</span>
      </div>
    </div>
  </section>

  <section class="card card--back" role="img" aria-label="Business card back with silver glitter texture and the Lunelle Rosa Hair name">
    <p class="wordmark">
      <span class="wordmark__line wordmark__line--lead">Lunelle Rosa</span>
      <span class="wordmark__line wordmark__line--sub">HAIR</span>
    </p>
  </section>

</main>
</body>
</html>
```